RWT Fittings Ltd Business Cards

We need a business card with our business logo. We provide window and door installations on high-rises in west coast British Colombia, Canada.

I would like my business information and details on one side of the card, and the other side the company name with logo

Target Market(s)

General Contractors

Industry/Entity Type

Construction

Contact Information for Business Card

one side i want my company name and logo in the dark theme logo that i provided

Requirements
Must have
• Marco Peltieri, 16045518293, RWTFittings@mailbox-demo.com, 1407-5194 Linden Row Burnaby BC, V5H 2K9, Owner & Manager

```html
<!DOCTYPE html>
<html lang="en">
<head>
<meta charset="UTF-8">
<title>RWT Fittings Ltd – Business Cards</title>
<link rel="stylesheet" href="https://fonts.googleapis.com/css2?family=Montserrat:wght@400;500;700&display=swap">
<style>
  :root {
    --backdrop: #b4b4b4;
    --card: #2b2b2b;
    --accent: #29a8e0;
    --grey: #9a9a9a;
    --ink: #e9e9e9;
  }
  * { box-sizing: border-box; margin: 0; padding: 0; }
  html, body { width: 1200px; height: 900px; overflow: hidden; }
  body {
    background: var(--backdrop);
    font-family: "Montserrat", Arial, sans-serif;
    display: flex;
    flex-direction: column;
    align-items: center;
    justify-content: center;
    gap: 40px;
  }
  .card {
    width: 640px;
    height: 366px;
    background: var(--card);
    border-bottom: 4px solid var(--accent);
    border-right: 2px solid var(--accent);
    box-shadow: 0 10px 24px rgba(0,0,0,0.35);
    position: relative;
  }
  /* Contact side */
  .card--contact {
    display: flex;
    align-items: center;
    padding: 0 40px 0 46px;
  }
  .brand {
    display: flex;
    align-items: center;
    gap: 12px;
  }
  .brand__mark {
    width: 26px;
    height: 26px;
    background: var(--grey);
  }
  .brand__name {
    color: var(--accent);
    font-weight: 700;
    letter-spacing: 0.5px;
  }
  .card--contact .brand { width: 248px; }
  .card--contact .brand__name { font-size: 22px; }
  .divider {
    width: 2px;
    height: 210px;
    background: var(--accent);
    margin-right: 26px;
  }
  .details { color: var(--ink); }
  .details__name {
    color: var(--accent);
    font-weight: 700;
    font-size: 24px;
    line-height: 1.1;
  }
  .details__role {
    font-size: 13px;
    margin-top: 4px;
  }
  .details__address {
    font-size: 13px;
    line-height: 1.4;
    margin-top: 28px;
  }
  .details__line {
    display: flex;
    align-items: center;
    gap: 10px;
    font-size: 13px;
    margin-top: 10px;
  }
  .details__line:first-of-type { margin-top: 26px; }
  .details__icon { width: 16px; height: 16px; flex: none; }
  /* Brand side */
  .card--brand {
    display: flex;
    align-items: center;
    justify-content: center;
  }
  .card--brand .brand { gap: 20px; }
  .card--brand .brand__mark { width: 54px; height: 54px; }
  .card--brand .brand__name { font-size: 46px; }
</style>
</head>
<body>
  <section class="card card--contact">
    <div class="brand">
      <span class="brand__mark"></span>
      <span class="brand__name">RWT Fittings Ltd</span>
    </div>
    <div class="divider"></div>
    <div class="details">
      <p class="details__name">Marco Peltieri</p>
      <p class="details__role">Owner &amp; Manager</p>
      <p class="details__address">1407-5194 Linden Row<br>Burnaby BC, V5H 2K9</p>
      <p class="details__line">
        <svg class="details__icon" viewBox="0 0 16 16" aria-hidden="true">
          <path d="M1 5 C1 2 15 2 15 5 L12 7 L10 5 L6 5 L4 7 Z" fill="var(--accent)"/>
          <rect x="3" y="8" width="10" height="7" rx="2" fill="var(--accent)"/>
          <circle cx="8" cy="11.5" r="1.8" fill="var(--card)"/>
        </svg>
        16045518293
      </p>
      <p class="details__line">
        <svg class="details__icon" viewBox="0 0 16 16" aria-hidden="true">
          <rect x="1" y="3" width="14" height="10" fill="var(--accent)"/>
          <path d="M1 3 L8 9 L15 3" fill="none" stroke="var(--card)" stroke-width="1.4"/>
        </svg>
        RWTFittings@mailbox-demo.com
      </p>
    </div>
  </section>

  <section class="card card--brand">
    <div class="brand">
      <span class="brand__mark"></span>
      <span class="brand__name">RWT Fittings Ltd</span>
    </div>
  </section>
</body>
</html>
```